Quintel Packaging Business Card

Project Overview
We are seeking a modern, minimalist business card that effectively represents our company while making a bold and lasting impression. The design should reflect trust, professionalism, and innovation, reinforcing our expertise in custom plastic manufacturing for warehouse and distribution centers.

Provided Assets & Specifications
Logo: We will provide our official logo for integration into the design.
Design Files: Photoshop (PSD) files for our printing specifications will be supplied.

Card Size & Material:
Dimensions: 3.5" x 2"
Material: 1/8" Radius Plastic Business Cards with 1/8" Rounded Corners
Clear plastic background—the design should strategically incorporate transparency.
Orientation: The card should be designed in landscape format for a sleek and professional presentation.

Design Requirements:
Logo Prominence
The logo must be the focal point of the card.
Space should be used effectively to draw attention to the logo while maintaining a minimalist layout.

Clear Plastic Integration
The transparent background should create the illusion of blank space, enhancing the modern and high-quality feel.
Avoid any frosted effects—we do not want white areas to appear semi-transparent.

Minimalist & Impactful
Clean, structured, and easy to read at a glance.
Focus on sharp contrast to ensure legibility and visibility.
The design should instill confidence and reflect our role as a leading plastics manufacturer.

Color Palette & Contrast
Primary Colors: Blue, Black, White, and Grey
Use bold black or blue for text and key elements to ensure they stand out against the clear plastic.
Avoid light, pastel, or neon colors that may fade into the plastic background.
No frosted or semi-transparent white—we do not want a cloudy effect.

Typography & Information Hierarchy
Bold, modern typography—clear, professional, and highly legible.
The business card should highlight:
Company Logo (Primary Focus)
Full Name & Title
Phone Number
Email
Website

Brand Representation
The card should reflect our expertise in manufacturing high-quality custom plastics for large-scale packaging and distribution businesses.
Our clients rely on us to enhance their brand presence through custom plastic solutions, and our business cards should reinforce that sense of precision and trust.

Final Considerations
Utilize the clear plastic effectively to differentiate our brand from standard business cards.
Maintain a sleek, professional aesthetic while ensuring all text and elements remain legible.
The design should align with our industry, conveying reliability and innovation.
We look forward to seeing a design that captures our brand identity, maximizes the clear plastic medium, and makes a strong, professional impact on our clients.

```html
<!DOCTYPE html>
<html lang="en">
<head>
<meta charset="utf-8">
<title>Quintel Packaging Business Card</title>
<link rel="stylesheet" href="https://fonts.googleapis.com/css2?family=Lato:wght@400;700&display=swap">
<style>
  :root {
    --page-bg: #e6ebf0;
    --card-bg: #fbfcfd;
    --card-edge: #cfd6dd;
    --ink: #333333;
    --ink-soft: #4a4a4a;
    --brand-blue: #2172a9;
    --band-dark: #3b3b3b;
  }
  * { margin: 0; padding: 0; box-sizing: border-box; }
  html, body {
    width: 1200px; height: 900px; overflow: hidden;
    background: var(--page-bg);
    font-family: "Lato", Arial, sans-serif;
  }
  .business-card {
    position: absolute; left: 77px; top: 152px;
    width: 1046px; height: 595px;
    background: var(--card-bg);
    border: 1px solid var(--card-edge);
    border-radius: 20px;
    overflow: hidden;
    box-shadow: 0 10px 30px rgba(40, 60, 80, 0.12);
    color: var(--ink);
  }
  .brand {
    position: absolute; right: 68px; top: 104px;
    display: flex; align-items: center; gap: 22px;
  }
  .brand-square {
    width: 86px; height: 86px; background: var(--brand-blue);
  }
  .brand-name {
    font-weight: 700; font-size: 46px; color: var(--ink);
    letter-spacing: 0.5px; white-space: nowrap;
  }
  .name-accent {
    position: absolute; left: 0; top: 277px;
    width: 15px; height: 87px; background: var(--brand-blue);
  }
  .person-name {
    position: absolute; left: 52px; top: 274px;
    font-weight: 700; font-size: 37px; color: var(--ink-soft);
    text-transform: uppercase; letter-spacing: 0.3px;
  }
  .person-title {
    position: absolute; left: 53px; top: 320px;
    font-size: 25px; color: var(--ink-soft);
  }
  .divider {
    position: absolute; left: 52px; top: 385px;
    width: 925px; height: 2px; background: var(--ink);
  }
  .contact-list {
    position: absolute; left: 58px; top: 412px;
    list-style: none;
  }
  .contact-item {
    display: flex; align-items: center; gap: 20px;
    height: 44px; font-size: 25px; color: var(--ink);
  }
  .contact-icon { width: 26px; height: 26px; flex: none; }
  .address {
    position: absolute; right: 68px; top: 454px;
    text-align: right; font-size: 25px; line-height: 40px; color: var(--ink);
  }
  .footer-bands { position: absolute; left: 0; bottom: 0; }
</style>
</head>
<body>
  <div class="business-card">
    <div class="brand">
      <div class="brand-square"></div>
      <div class="brand-name">Quintel Packaging</div>
    </div>

    <div class="name-accent"></div>
    <div class="person-name">Marcus Hale</div>
    <div class="person-title">Owner</div>
    <div class="divider"></div>

    <ul class="contact-list">
      <li class="contact-item">
        <svg class="contact-icon" viewBox="0 0 24 24" aria-hidden="true">
          <path fill="var(--brand-blue)" d="M6.6 10.8a15.1 15.1 0 0 0 6.6 6.6l2.2-2.2a1 1 0 0 1 1-.25 11.4 11.4 0 0 0 3.6.57 1 1 0 0 1 1 1V20a1 1 0 0 1-1 1A17 17 0 0 1 3 4a1 1 0 0 1 1-1h3.5a1 1 0 0 1 1 1c0 1.25.2 2.45.57 3.57a1 1 0 0 1-.25 1z"/>
        </svg>
        <span>044-987 654 321</span>
      </li>
      <li class="contact-item">
        <svg class="contact-icon" viewBox="0 0 24 24" aria-hidden="true">
          <path fill="var(--brand-blue)" d="M2 5h20v14H2z"/>
          <path fill="none" stroke="var(--card-bg)" stroke-width="1.8" d="M2.5 5.8 12 13l9.5-7.2"/>
        </svg>
        <span>hello@quintelpack.com</span>
      </li>
      <li class="contact-item">
        <svg class="contact-icon" viewBox="0 0 24 24" aria-hidden="true">
          <circle cx="12" cy="12" r="10" fill="var(--brand-blue)"/>
          <path fill="none" stroke="var(--card-bg)" stroke-width="1.4" d="M2 12h20M12 2c3 3 3 17 0 20M12 2c-3 3-3 17 0 20"/>
        </svg>
        <span>www.quintelpack.com</span>
      </li>
    </ul>

    <div class="address">421, Address line goes<br>here 45452, Country name</div>

    <svg class="footer-bands" width="1046" height="24" viewBox="0 0 1046 24" aria-hidden="true">
      <polygon points="0,0 540,0 516,24 0,24" fill="var(--band-dark)"/>
      <polygon points="556,0 1046,0 1046,24 532,24" fill="var(--brand-blue)"/>
    </svg>
  </div>
</body>
</html>
```